Brightway Carpet and Tile cleaning Business card Design

I need a design that has the same feel as my van.
i would also like a prominent "Review us on facebook" somewhere, but not that it makes it look silly.
I would like the card to have a little bit of grey or black in the design as well.

It will need contact details
phone: 0455 817264
email: rkbrightwayclean@mailbox-example.com
website: www.brightwaycarpetandtilecleaning-example.com.au
facebook: /brightwaycarpetandtilecleaning

Industry/Entity Type

Business

Contact Information for Business Card

Phone number 0455817264
Email rkbrightwayclean@mailbox-example.com
Website www.brightwaycarpetandtilecleaning-example.com.au
Facebook/brightwaycarpetandtilecleaning

Colors
000000

Requirements
Must have
• Same feel as my van
• I want the card to stand out from the crowd
Nice to have
• Maybe include a tiny bit of a third colour? Grey's,blacks, orange?

```html
<!DOCTYPE html>
<html lang="en">
<head>
<meta charset="utf-8">
<title>Brightway Carpet and Tile Cleaning – Business Card</title>
<link href="https://fonts.googleapis.com/css2?family=Arimo:wght@400;700&family=Open+Sans:wght@400;600&display=swap" rel="stylesheet">
<style>
  :root {
    --stage: #3f3f3f;
    --card-white: #ffffff;
    --aqua: #1fc8ea;
    --aqua-light: #7fe6fa;
    --aqua-deep: #0aa6d4;
    --lime: #7cc242;
    --steel: #8a8d90;
    --ink: #555a5e;
    --night: #050607;
    --button-top: #8aa4de;
    --button-bottom: #3c5fb4;
    --button-edge: #24397a;
  }
  * { box-sizing: border-box; margin: 0; padding: 0; }
  html, body { width: 1105px; height: 1200px; overflow: hidden; }
  body { background: var(--stage); position: relative; font-family: "Open Sans", sans-serif; }

  .card { position: absolute; left: 196px; width: 720px; height: 412px; overflow: hidden; box-shadow: 0 4px 14px rgba(0,0,0,.45); }
  .card--front { top: 145px; background: var(--card-white); }
  .card--back { top: 602px; background: var(--night); }

  .front-swoosh { position: absolute; inset: 0; width: 720px; height: 412px; }

  .holder { position: absolute; left: 28px; top: 88px; color: #fff; font-family: "Arimo", sans-serif; }
  .holder__name { font-size: 26px; font-weight: 700; letter-spacing: .5px; }
  .holder__role { font-size: 17px; font-weight: 400; margin-top: 8px; letter-spacing: .3px; }

  .brand { position: absolute; display: flex; align-items: center; gap: 12px; font-family: "Arimo", sans-serif; font-weight: 700; }
  .brand__dot { border-radius: 50%; background: var(--aqua); flex: none; }
  .brand--front { left: 372px; top: 160px; }
  .brand--front .brand__name { font-size: 38px; color: var(--aqua-deep); }
  .brand--front .brand__dot { width: 26px; height: 26px; }

  .contacts { position: absolute; right: 54px; top: 256px; list-style: none; text-align: right; }
  .contacts li { display: flex; justify-content: flex-end; align-items: center; gap: 14px; height: 30.5px; font-size: 16px; color: var(--ink); }
  .contacts svg { width: 18px; height: 18px; flex: none; }

  .back-bokeh { position: absolute; inset: 0; background:
      radial-gradient(circle at 70% 40%, rgba(60,80,60,.45), transparent 45%),
      radial-gradient(circle at 20% 75%, rgba(40,70,70,.4), transparent 40%),
      linear-gradient(100deg, #000 0%, #0b0d0e 60%, #2a2c2e 75%, #050505 100%); }

  .brand--back { left: 0; right: 0; top: 158px; justify-content: center; }
  .brand--back .brand__name { font-size: 58px; color: var(--aqua); }
  .brand--back .brand__dot { width: 34px; height: 34px; }

  .review { position: absolute; left: 200px; top: 322px; display: flex; align-items: center; gap: 8px; }
  .review__button { width: 260px; height: 38px; border: 2px solid var(--button-edge); border-radius: 3px;
      background: linear-gradient(var(--button-top), var(--button-bottom));
      font-family: "Arimo", sans-serif; font-weight: 700; font-size: 26px; color: #0c1430;
      display: flex; align-items: center; justify-content: center; letter-spacing: .5px; }
  .review__mark { width: 46px; height: 46px; border-radius: 6px; background: var(--button-bottom); border: 2px solid var(--button-top); }
</style>
</head>
<body>

<section class="card card--front" aria-label="Business card front">
  <svg class="front-swoosh" viewBox="0 0 720 412" aria-hidden="true">
    <defs>
      <linearGradient id="aqua-fill" x1="0" y1="0" x2="1" y2="1">
        <stop offset="0" stop-color="#7fe6fa"/>
        <stop offset=".5" stop-color="#1fc8ea"/>
        <stop offset="1" stop-color="#0aa6d4"/>
      </linearGradient>
    </defs>
    <path d="M0 0 H600 C410 40 200 210 140 412 H0 Z" fill="#7cc242"/>
    <path d="M0 0 H588 C396 40 186 210 124 412 H0 Z" fill="url(#aqua-fill)" role="img" aria-label="Soft aqua band where floating soap bubbles belong"/>
    <path d="M0 58 C110 18 230 4 340 0 H0 Z" fill="#8a8d90"/>
    <path d="M0 68 C120 24 250 8 380 0 H360 C240 6 120 22 0 60 Z" fill="#ffffff" opacity=".6"/>
  </svg>

  <div class="holder">
    <p class="holder__name">RYAN KELLETT</p>
    <p class="holder__role">OWNER/OPERATOR</p>
  </div>

  <div class="brand brand--front">
    <span class="brand__dot"></span>
    <span class="brand__name">Brightway Clean</span>
  </div>

  <ul class="contacts">
    <li>0455817264
      <svg viewBox="0 0 24 24"><path fill="#1fc8ea" d="M6.6 10.8a15 15 0 0 0 6.6 6.6l2.2-2.2c.3-.3.7-.4 1-.2 1.1.4 2.3.6 3.6.6.6 0 1 .4 1 1V20c0 .6-.4 1-1 1A17 17 0 0 1 3 4c0-.6.4-1 1-1h3.5c.6 0 1 .4 1 1 0 1.3.2 2.5.6 3.6.1.3 0 .7-.2 1z"/></svg>
    </li>
    <li>rkbrightwayclean@mailbox-example.com
      <svg viewBox="0 0 24 24"><rect x="2" y="5" width="20" height="14" rx="1" fill="#1fc8ea"/><path d="M2 6l10 7 10-7" fill="none" stroke="#fff" stroke-width="1.6"/></svg>
    </li>
    <li>www.brightwaycarpetandtilecleaning-example.com.au
      <svg viewBox="0 0 24 24"><circle cx="12" cy="12" r="10" fill="#1fc8ea"/><path d="M2 12h20M12 2c3 3 3 17 0 20M12 2c-3 3-3 17 0 20" fill="none" stroke="#fff" stroke-width="1.3"/></svg>
    </li>
    <li>brightwaycarpetandtilecleaning
      <svg viewBox="0 0 24 24"><rect x="3" y="3" width="18" height="18" rx="2" fill="#1fc8ea"/></svg>
    </li>
  </ul>
</section>

<section class="card card--back" aria-label="Business card back">
  <div class="back-bokeh" role="img" aria-label="Dark background with soft glowing bubbles and sparkles"></div>

  <div class="brand brand--back">
    <span class="brand__dot"></span>
    <span class="brand__name">Brightway Clean</span>
  </div>

  <div class="review">
    <span class="review__button">REVIEW US ON</span>
    <span class="review__mark"></span>
  </div>
</section>

</body>
</html>
```